Wordpress 6 pages GLAM design for hair salon

Hi guys.
I need a glam & easy to navigate web design for my (women only) new hair salon.
I have a logo. You can see in attached files.
I like 3d backgrounds.
My favourite colours choice: any variety of pink(hot & very soft), white, black, grey.
I would like to see website very feminine, glamorous & kind of old Hollywood and Dorinda Calloway inspired.
Of course it should have plug ins, like social media, map, security etc.
My website now: http://velmoracoiffure.example

Designs what I like:
http://torvinellastudio.example
http://pelurabeautyloft.example
http://www.quillfernvisualworks.example/boutique-graphic-web-folio.html
Updates

Target Market(s)

WOMEN

Industry/Entity Type

Boutique

Requirements
Should not have
• any cartoon or other characters!

```html
<!DOCTYPE html>
<html lang="en">
<head>
<meta charset="utf-8">
<title>Velmora Coiffure</title>
<link href="https://fonts.googleapis.com/css2?family=Arimo:wght@400&family=Open+Sans:wght@300;400&family=Source+Sans+3:wght@400;600&display=swap" rel="stylesheet">
<style>
:root{
  --pink:#c54a80;
  --pink-dark:#b23d70;
  --pink-line:#d77aa3;
  --ink:#4a4a4a;
  --muted:#777;
  --page:#efefef;
  --header:#f7f7f7;
  --footer:#333333;
  --cal-head:#3c3c3c;
  --cal-line:#e3e3e3;
  --today:#2f63e6;
}
*{margin:0;padding:0;box-sizing:border-box}
html,body{width:840px;height:1200px;overflow:hidden}
body{position:relative;background:var(--page);font-family:"Open Sans",sans-serif;color:var(--ink)}
.header{position:absolute;left:0;top:0;width:840px;height:143px;background:var(--header)}
.brand{position:absolute;left:62px;top:50px;display:flex;align-items:center;gap:10px}
.brand-dot{width:30px;height:30px;border-radius:50%;background:var(--pink)}
.brand-name{font-family:"Source Sans 3",sans-serif;font-weight:600;font-size:24px;color:var(--pink);letter-spacing:1px;text-transform:uppercase}
.search{position:absolute;left:596px;top:61px;width:183px;height:26px;border:1px solid #d6d6d6;background:#fff;font-family:"Arimo",sans-serif;font-size:11px;color:#888;padding:6px 9px}
.search svg{position:absolute;right:7px;top:7px}
.nav{position:absolute;left:0;top:143px;width:840px;height:33px;background:linear-gradient(#cf5c8d,var(--pink-dark));border-top:1px solid var(--pink-line)}
.nav a{position:absolute;top:0;height:33px;line-height:33px;font-family:"Arimo",sans-serif;font-size:12.5px;color:#fff;text-decoration:none}
.nav .sep{position:absolute;top:0;width:1px;height:33px;background:#a8346a;border-right:1px solid var(--pink-line)}
.hero{position:absolute;left:0;top:176px;width:840px;height:364px;background:linear-gradient(100deg,#7a2a10 0%,#b84a1c 30%,#d9895e 55%,#c0542a 75%,#8a3212 100%)}
.hero-title{position:absolute;left:138px;top:230px;font-family:"Source Sans 3",sans-serif;font-weight:600;font-size:28px;color:#fff;letter-spacing:-.3px}
.hero-sub{position:absolute;left:138px;top:271px;font-family:"Source Sans 3",sans-serif;font-size:20px;color:#fff;letter-spacing:-.3px}
.hero-arrow{position:absolute;top:240px}
.dots{position:absolute;left:398px;top:346px;display:flex;gap:4px}
.dots span{width:9px;height:9px;border-radius:50%;background:#eee;box-shadow:inset 0 1px 2px rgba(0,0,0,.3)}
.dots span:first-child{background:#999}
.welcome-title{position:absolute;left:61px;top:573px;font-family:"Open Sans",sans-serif;font-weight:300;font-size:14px;color:var(--pink);letter-spacing:-.3px}
.welcome-photo{position:absolute;left:60px;top:610px;width:142px;height:156px;background:linear-gradient(135deg,#c9a98a,#7d5a40 60%,#a8866b)}
.welcome-text{position:absolute;left:218px;top:610px;width:314px;font-weight:300;font-size:9.8px;line-height:16.8px;color:#555}
.welcome-text p+p{margin-top:2px}
.calendar{position:absolute;left:577px;top:576px;width:202px;background:#fff;border:1px solid #ddd}
.cal-head{height:30px;background:linear-gradient(#4a4a4a,var(--cal-head));color:#fff;font-family:"Source Sans 3",sans-serif;font-weight:600;font-size:12px;text-align:center;line-height:30px;position:relative}
.cal-head svg{position:absolute;top:10px}
.cal-grid{display:grid;grid-template-columns:repeat(7,1fr)}
.cal-grid .dn{height:17px;font-size:6.5px;color:#777;text-align:center;line-height:17px;border-bottom:1px solid var(--cal-line)}
.cal-grid .d{height:28.5px;font-size:8px;font-weight:400;color:#333;text-align:center;line-height:28px;border-right:1px solid var(--cal-line);border-bottom:1px solid var(--cal-line);position:relative}
.cal-grid .d.off{color:#aaa}
.cal-grid .d.ev::after{content:"";position:absolute;left:50%;bottom:6px;width:2px;height:2px;margin-left:-1px;background:#333;border-radius:50%}
.cal-grid .d.today{background:var(--today);color:#fff;box-shadow:inset 0 0 0 2px #1b45b8}
.cal-grid .d.today::after{background:#fff}
.feature{position:absolute;top:829px;width:220px;text-align:center}
.feature-photo{width:136px;height:136px;margin:0 auto;border-radius:50%;border:6px solid #fff;box-shadow:0 1px 4px rgba(0,0,0,.15)}
.feature h2{margin-top:13px;font-family:"Source Sans 3",sans-serif;font-weight:400;font-size:16px;color:var(--pink);letter-spacing:.3px}
.feature p{margin-top:7px;font-size:10.5px;line-height:17.6px;color:#555}
.btn{display:inline-block;margin-top:8px;width:49px;height:22px;line-height:22px;background:linear-gradient(#8a8a8a,#555);border-radius:2px;color:#fff;font-family:"Source Sans 3",sans-serif;font-size:11px}
.footer{position:absolute;left:0;top:1115px;width:840px;height:85px;background:var(--footer);font-family:"Arimo",sans-serif;font-size:10px;color:#fff}
.footer-links{position:absolute;left:61px;top:22px}
.copyright{position:absolute;left:61px;top:47px}
.social{position:absolute;left:637px;top:31px;display:flex;gap:9px}
.social span{width:25px;height:25px}
</style>
</head>
<body>
<header class="header">
  <div class="brand"><span class="brand-dot"></span><span class="brand-name">Velmora Coiffure</span></div>
  <div class="search">Search..
    <svg width="11" height="11" viewBox="0 0 11 11"><circle cx="4.5" cy="4.5" r="3.5" fill="none" stroke="#999" stroke-width="1.3"/><line x1="7" y1="7" x2="10" y2="10" stroke="#999" stroke-width="1.5"/></svg>
  </div>
</header>
<nav class="nav">
  <a style="left:60px">HOME</a><span class="sep" style="left:102px"></span>
  <a style="left:116px">ABOUT US</a><span class="sep" style="left:182px"></span>
  <a style="left:203px">SERVICES</a><span class="sep" style="left:272px"></span>
  <a style="left:292px">GALLERY</a><span class="sep" style="left:359px"></span>
  <a style="left:382px">BLOG</a><span class="sep" style="left:429px"></span>
  <a style="left:449px">CONTACT US</a>
</nav>
<section class="hero" role="img" aria-label="Close-up of a woman with long flowing copper-red hair">
  <svg class="hero-arrow" style="left:40px" width="18" height="36" viewBox="0 0 18 36"><polyline points="16,2 2,18 16,34" fill="none" stroke="#fff" stroke-opacity=".7" stroke-width="1.3"/></svg>
  <svg class="hero-arrow" style="left:784px" width="18" height="36" viewBox="0 0 18 36"><polyline points="2,2 16,18 2,34" fill="none" stroke="#fff" stroke-opacity=".7" stroke-width="1.3"/></svg>
  <div class="hero-title">NAM LIBER TEMPOR CUM SOLUTA</div>
  <div class="hero-sub">ELEIFEND OPTION CONGUE NIHIL IMPERDIET</div>
  <div class="dots"><span></span><span></span><span></span><span></span></div>
</section>
<h1 class="welcome-title">WELCOME TO OUR WEBSITE</h1>
<div class="welcome-photo" role="img" aria-label="Woman with long straight brown hair in profile"></div>
<div class="welcome-text">
  <p>Ut wisi enim ad minim veniam, quis nostrud exerci tation ullamcorper suscipt nisl ut aliquip ex ea commodo consequat. Duis autem vel eum iriure dolor in it in vulputate velit esse molestie consequat, vel illum dolore eu feugiat nuafa vero eros et accumsan et iusto odio dignissim qui blandit praesent luptatumz enit augue duis dolore te feugait nulla facilisi. Nam liber tempor cum solutano fend option congue nihl imperdiet doming id quiod mazim placerat facer.</p>
  <p>Typi non habent claritatem insitam; est usus legentis in iis qui facit eorum cla Investigationes demonstraverunt lectores legere me lius quod ii legunt saepi us. Claritas est etiam processus dynamicus, qui sequitur mutationem.</p>
</div>
<aside class="calendar">
  <div class="cal-head">
    <svg style="left:12px" width="6" height="10" viewBox="0 0 6 10"><polyline points="5,1 1,5 5,9" fill="none" stroke="#fff" stroke-width="1.8"/></svg>
    January 2014
    <svg style="right:12px" width="6" height="10" viewBox="0 0 6 10"><polyline points="1,1 5,5 1,9" fill="none" stroke="#fff" stroke-width="1.8"/></svg>
  </div>
  <div class="cal-grid">
    <span class="dn">MON</span><span class="dn">TUE</span><span class="dn">WED</span><span class="dn">THU</span><span class="dn">FRI</span><span class="dn">SAT</span><span class="dn">SUN</span>
    <span class="d off ev">30</span><span class="d">1</span><span class="d ev">2</span><span class="d">3</span><span class="d">4</span><span class="d">5</span><span class="d">6</span>
    <span class="d">7</span><span class="d">8</span><span class="d">9</span><span class="d">10</span><span class="d">11</span><span class="d today ev">12</span><span class="d">13</span>
    <span class="d">14</span><span class="d">15</span><span class="d ev">16</span><span class="d ev">17</span><span class="d">18</span><span class="d">19</span><span class="d">20</span>
    <span class="d ev">21</span><span class="d">22</span><span class="d">23</span><span class="d">24</span><span class="d">25</span><span class="d">26</span><span class="d">27</span>
    <span class="d">28</span><span class="d">29</span><span class="d">30</span><span class="d">31</span><span class="d off">1</span><span class="d off">2</span><span class="d off">3</span>
  </div>
</aside>
<section class="feature" style="left:50px">
  <div class="feature-photo" role="img" aria-label="Portrait of a woman with a short dark haircut" style="background:radial-gradient(circle at 50% 55%,#d8c4b8,#2a2220 75%)"></div>
  <h2>OUR SERVICES</h2>
  <p>Vivamus vel eros eet mgna volutpat sagi tts. Nulla faucibus nibh a mgna tinciunt accu msan amet ante hndrerit</p>
  <span class="btn">MORE</span>
</section>
<section class="feature" style="left:305px">
  <div class="feature-photo" role="img" aria-label="Portrait of a woman with wavy golden-brown hair" style="background:radial-gradient(circle at 50% 55%,#c9925e,#5a3418 80%)"></div>
  <h2>RECENT POSTS</h2>
  <p>Vivamus vel eros eet mgna volutpat sagi tis. Nulla faucibus nibh a mgna tinciunt accu msan amet ante hndrerit</p>
  <span class="btn">MORE</span>
</section>
<section class="feature" style="left:559px">
  <div class="feature-photo" role="img" aria-label="Portrait of a woman with long dark hair" style="background:radial-gradient(circle at 50% 55%,#dcbca8,#2e2622 75%)"></div>
  <h2>BEAUTY CLINIC</h2>
  <p>Vivamus vel eros eget magna volutpat sagi ttis. Nulla faucibus nibh a magna tincidunt accu msan amet ante hendrerit</p>
  <span class="btn">MORE</span>
</section>
<footer class="footer">
  <div class="footer-links">Home | About Us | Services | Gallery | Blog | Contact Us</div>
  <div class="copyright">Copyright © 2013. All Rights Reserved.</div>
  <div class="social">
    <span style="background:#3b5ba8" aria-label="Social profile"></span>
    <span style="background:#2d9fd8" aria-label="Social profile"></span>
    <span style="background:#f07a1a" aria-label="News feed"></span>
    <span style="background:#d9262b" aria-label="Video channel"></span>
  </div>
</footer>
</body>
</html>
```